ULMIRA card Technical Architecture

Hello everyone ULMIRA: It is a consulting firm in Architecture and Construction. I require a card duplexing, sober, elegant, classic but not boring. Update 1: Use the following data for the card. Name: Gonzalo Pereda Mauricio Villalta Position: COO Twitter: @ulmiraAT Homepage: ulmira-example.com home address not include the participation of all thank you.

Target Market(s)

Construction companies, Architects and Consulting Engineers

Industry/Entity Type

Consulting

Contact Information for Business Card

Los campos que debe tener:
Nombre, Cargo, email, homepage y twitter

Font styles to use
Serif
Sans Serif
Other font styles liked:
• Me gustan playfair display, open sans y roboto, pero estoy sujeto a sus propuestas

Requirements
Must have
• Colors: Present combined proposals in white, red, gray and black Update 1: The two names must be clearly differentiated from the two surnames
Nice to have
• They are free to present their best proposals. I will bring them immediate feedback to the extent you can go see their designs. Complete data for card and logo files will give the winner the

```html
<!DOCTYPE html>
<html lang="es">
<head>
<meta charset="utf-8">
<title>ULMIRA – Tarjeta de presentación</title>
<link rel="stylesheet" href="https://fonts.googleapis.com/css2?family=Questrial&family=Lato:wght@300;400;700;900&display=swap">
<style>
  :root {
    --bg: #1c1c1c;
    --card-white: #f6f6f6;
    --brand-red: #8e1016;
    --brand-red-deep: #6a0a0e;
    --brand-red-light: #a3161d;
    --name-red: #9a2a2e;
    --ink-gray: #555555;
    --ink-dark: #2a2a2a;
    --soft-line: #b9a3a4;
    --white: #ffffff;
  }
  * { box-sizing: border-box; margin: 0; padding: 0; }
  html, body { width: 1200px; height: 873px; overflow: hidden; }
  body {
    position: relative;
    background: var(--bg);
    font-family: "Lato", sans-serif;
  }
  .card {
    position: absolute;
    width: 520px;
    height: 297px;
    border-radius: 14px;
    overflow: hidden;
  }

  /* Front: white side */
  .card-front {
    left: 80px;
    top: 130px;
    background: var(--card-white);
  }
  .front-logo {
    position: absolute;
    left: 40px;
    top: 96px;
    width: 230px;
  }
  .wordmark {
    display: flex;
    align-items: center;
    gap: 12px;
    font-family: "Questrial", sans-serif;
    font-size: 36px;
    letter-spacing: 10px;
    color: var(--ink-gray);
    line-height: 1;
  }
  .wordmark-mark {
    width: 14px;
    height: 14px;
    background: var(--brand-red);
    flex: none;
  }
  .front-logo .rule {
    height: 1px;
    background: var(--soft-line);
    margin: 8px 0 5px;
  }
  .tagline {
    font-family: "Questrial", sans-serif;
    font-size: 11px;
    letter-spacing: 3.6px;
    color: var(--brand-red);
  }
  .contact-list {
    position: absolute;
    left: 40px;
    bottom: 34px;
    list-style: none;
    font-size: 14px;
    color: var(--ink-dark);
  }
  .contact-list li {
    display: flex;
    align-items: center;
    gap: 10px;
    margin-top: 6px;
  }
  .contact-list svg { width: 13px; height: 13px; flex: none; }
  .people {
    position: absolute;
    right: 40px;
    top: 36px;
    text-align: right;
  }
  .person { margin-bottom: 14px; }
  .person-name {
    font-size: 16px;
    color: var(--name-red);
    line-height: 1.2;
  }
  .given-name {
    font-weight: 300;
    color: var(--ink-gray);
  }
  .surname {
    font-weight: 900;
    color: var(--name-red);
    text-transform: uppercase;
    letter-spacing: 0.5px;
    font-size: 14px;
  }
  .person-role {
    font-size: 10px;
    letter-spacing: 1px;
    color: var(--ink-gray);
    margin-top: 2px;
  }

  /* Back: red side */
  .card-back {
    left: 600px;
    top: 446px;
  }
  .back-surface {
    position: absolute;
    inset: 0;
    background: linear-gradient(135deg, var(--brand-red-light) 0%, var(--brand-red) 45%, var(--brand-red-deep) 100%);
  }
  .back-logo {
    position: absolute;
    left: 46px;
    top: 150px;
    width: 320px;
  }
  .back-logo .wordmark {
    color: var(--white);
    font-size: 44px;
    letter-spacing: 14px;
  }
  .back-logo .wordmark-mark { background: var(--white); }
  .back-logo .rule {
    height: 1px;
    background: rgba(255,255,255,0.45);
    margin: 8px 0 6px;
  }
  .back-logo .tagline {
    color: rgba(255,255,255,0.85);
    font-size: 13px;
    letter-spacing: 4.6px;
  }
  .web {
    font-family: "Questrial", sans-serif;
    font-size: 13px;
    letter-spacing: 3px;
    color: #1a0304;
    margin-top: 6px;
  }
</style>
</head>
<body>

  <section class="card card-front" aria-label="Tarjeta, cara frontal">
    <div class="front-logo">
      <div class="wordmark"><span class="wordmark-mark"></span>ULMIRA</div>
      <div class="rule"></div>
      <div class="tagline">ARQUITECTURA TÉCNICA</div>
    </div>

    <div class="people">
      <div class="person">
        <div class="person-name"><span class="given-name">Gonzalo</span> <span class="surname">Pereda</span></div>
        <div class="person-role">COO</div>
      </div>
      <div class="person">
        <div class="person-name"><span class="given-name">Mauricio</span> <span class="surname">Villalta</span></div>
        <div class="person-role">COO</div>
      </div>
    </div>

    <ul class="contact-list">
      <li>
        <svg viewBox="0 0 14 14" aria-hidden="true"><circle cx="7" cy="7" r="6" fill="var(--brand-red)"/></svg>
        @ulmiraAT
      </li>
      <li>
        <svg viewBox="0 0 14 14" aria-hidden="true"><path d="M3 1.5l2.2 0 1 3-1.4 1a7 7 0 0 0 3.7 3.7l1-1.4 3 1 0 2.2c0 .8-.7 1.5-1.5 1.5A10.5 10.5 0 0 1 1.5 3 1.5 1.5 0 0 1 3 1.5z" fill="var(--brand-red)"/></svg>
        555-013-7120
      </li>
      <li>
        <svg viewBox="0 0 14 14" aria-hidden="true"><rect x="1" y="3" width="12" height="8.5" rx="1" fill="var(--brand-red)"/><path d="M1.5 3.5L7 8l5.5-4.5" fill="none" stroke="var(--card-white)" stroke-width="1.1"/></svg>
        contactus@ulmira-example.com
      </li>
    </ul>
  </section>

  <section class="card card-back" aria-label="Tarjeta, cara posterior">
    <div class="back-surface" role="img" aria-label="Fondo rojo con patrón geométrico facetado"></div>
    <div class="back-logo">
      <div class="wordmark"><span class="wordmark-mark"></span>ULMIRA</div>
      <div class="rule"></div>
      <div class="tagline">ARQUITECTURA TÉCNICA</div>
      <div class="web">www.ulmira-example.com</div>
    </div>
  </section>

</body>
</html>
```